KBT Business Cards

We require business cards for our business. We would like a matte black back to the card, with our logo centred in the middle. The front side of the card is open to design.

Target Market(s)

Clients looking for legal services (professional)

Industry/Entity Type

Legal

Contact Information for Business Card

Doran Kelbrath
Partner
Mobile: 0461 738 524
Email: doran@kbtlaw.co
Website: www.kbtlaw.co
Level 3, 118 Wendmore Street
Sydney NSW 2000

Font styles to use
Other font styles liked:
• Avenir

Colors
f04a50
ffffff
1b1b1b

Requirements
Must have
• Black back with logo included in the centre of the card.
• Our font is Avenir.

```html
<!DOCTYPE html>
<html lang="en">
<head>
<meta charset="utf-8">
<title>KBT Legal – Business Cards</title>
<link href="https://fonts.googleapis.com/css2?family=Montserrat:wght@400;500;600;700&display=swap" rel="stylesheet">
<style>
  :root {
    --stage: #1c1c1c;
    --paper: #e9e9e9;
    --ink: #1b1b1b;
    --brand-red: #c11f43;
    --brand-red-bright: #d9274d;
    --back-card: #0f0f0f;
    --back-mark: #2b2b2b;
    --white: #ffffff;
  }
  * { margin: 0; padding: 0; box-sizing: border-box; }
  html, body {
    width: 1200px; height: 1200px; overflow: hidden;
    background: var(--stage);
    font-family: "Montserrat", Arial, sans-serif;
  }
  .canvas { position: relative; width: 1200px; height: 1200px; }

  .card {
    position: absolute; left: 227px; width: 746px; height: 424px; overflow: hidden;
  }
  .card--front { top: 136px; background: var(--paper); }
  .card--back { top: 640px; background: var(--back-card); }

  .front__texture {
    position: absolute; right: 0; top: 0; width: 380px; height: 340px;
    background: radial-gradient(ellipse at 70% 45%, rgba(200,200,200,0.45), rgba(233,233,233,0) 70%);
  }

  .wordmark { position: absolute; display: flex; align-items: center; gap: 18px; }
  .wordmark__square { width: 44px; height: 44px; background: var(--brand-red); }
  .wordmark__name {
    font-weight: 700; font-size: 40px; letter-spacing: 0.5px; color: var(--ink); line-height: 1;
  }
  .card--front .wordmark { left: 37px; top: 68px; }
  .card--back .wordmark { left: 50%; top: 50%; transform: translate(-50%, -50%); gap: 26px; }
  .card--back .wordmark__square { width: 64px; height: 64px; background: var(--back-mark); }
  .card--back .wordmark__name { font-size: 60px; color: var(--back-mark); }

  .person { position: absolute; left: 37px; top: 212px; }
  .person__name { font-weight: 600; font-size: 24px; color: var(--brand-red); letter-spacing: 0.6px; }
  .person__role { font-size: 17px; color: var(--ink); margin-top: 2px; letter-spacing: 0.4px; }

  .contact { position: absolute; left: 37px; top: 278px; list-style: none; }
  .contact__item {
    display: flex; align-items: center; gap: 9px;
    font-size: 17.5px; color: var(--ink); height: 24px; letter-spacing: 0.3px;
  }
  .contact__icon { width: 18px; height: 18px; }

  .band { position: absolute; left: 0; top: 349px; width: 100%; height: 38px; display: flex; }
  .band__address {
    flex: 0 0 521px; background: var(--ink); color: #e6e6e6;
    font-size: 17px; letter-spacing: 0.4px; display: flex; align-items: center; padding-left: 33px;
  }
  .band__web {
    flex: 1; background: linear-gradient(90deg, #8e1730, var(--brand-red) 40%, var(--brand-red-bright));
    color: var(--white); font-size: 17px; letter-spacing: 0.4px;
    display: flex; align-items: center; justify-content: flex-end; padding-right: 34px;
  }
</style>
</head>
<body>
<main class="canvas">
  <section class="card card--front" aria-label="Business card front">
    <div class="front__texture" role="img" aria-label="Faint tonal background decoration"></div>

    <div class="wordmark">
      <span class="wordmark__square"></span>
      <span class="wordmark__name">KBT LEGAL</span>
    </div>

    <div class="person">
      <h1 class="person__name">Doran Kelbrath</h1>
      <p class="person__role">Partner</p>
    </div>

    <ul class="contact">
      <li class="contact__item">
        <svg class="contact__icon" viewBox="0 0 18 18" aria-hidden="true">
          <circle cx="9" cy="9" r="9" fill="var(--brand-red)"/>
          <path d="M4.5 7.2c0-1.4 2-2.4 4.5-2.4s4.5 1 4.5 2.4l-1.6.6-.4-1.2H6.5l-.4 1.2z" fill="#fff"/>
          <rect x="5.5" y="8.2" width="7" height="4.6" rx="1" fill="#fff"/>
          <circle cx="9" cy="10.5" r="1.3" fill="var(--brand-red)"/>
        </svg>
        <span>0461 738 524</span>
      </li>
      <li class="contact__item">
        <svg class="contact__icon" viewBox="0 0 18 18" aria-hidden="true">
          <circle cx="9" cy="9" r="9" fill="var(--brand-red)"/>
          <rect x="4.5" y="5.8" width="9" height="6.4" fill="none" stroke="#fff" stroke-width="1.2"/>
          <path d="M4.8 6.2L9 9.6l4.2-3.4M4.8 11.8l3-2.6M13.2 11.8l-3-2.6" fill="none" stroke="#fff" stroke-width="1"/>
        </svg>
        <span>doran@kbtlaw.co</span>
      </li>
    </ul>

    <div class="band">
      <p class="band__address">Level 3, 118 Wendmore Street Sydney NSW 2000</p>
      <p class="band__web">www.kbtlaw.co</p>
    </div>
  </section>

  <section class="card card--back" aria-label="Business card back">
    <div class="wordmark">
      <span class="wordmark__square"></span>
      <span class="wordmark__name">KBT LEGAL</span>
    </div>
  </section>
</main>
</body>
</html>
```